Cedar Brook Stables, LLC

Equestrian business card to promote equine retirement, farm sitting, short term board. Located in Ashford, SC.
Updates
Updated color schemes.
Contact Information for Business Card
Contact info, description of work.
Colors
0094D4
00A9DD
6FCCEA
C7EBF8
E9F6FB
59FF00
82FF00
B8FF75
E3FFCB
F4FFEA
F0912C
F2A743
F7CA91
FBE8D2
FDF5EE

```html
<!DOCTYPE html>
<html lang="en">
<head>
<meta charset="utf-8">
<title>Cedar Brook Stables – Business Card</title>
<link href="https://fonts.googleapis.com/css2?family=Crimson+Text:wght@400;600;700&display=swap" rel="stylesheet">
<style>
  :root {
    --backdrop: #2b2b2b;
    --card: #f2ede9;
    --ink: #0d0d0d;
    --ink-soft: #2a2a2a;
    --band-text: #f2ede9;
    --art-light: #efe9e4;
    --art-dark: #dcd4cd;
  }
  * { box-sizing: border-box; margin: 0; padding: 0; }
  html, body {
    width: 1200px; height: 962px; overflow: hidden;
    background: var(--backdrop);
    font-family: "Crimson Text", Georgia, serif;
    color: var(--ink);
  }
  .canvas { position: relative; width: 1200px; height: 962px; }
  .card {
    position: absolute;
    left: 320px;
    width: 560px; height: 320px;
    background: var(--card);
    border-radius: 22px;
    overflow: hidden;
    box-shadow: 0 8px 24px rgba(0,0,0,.35);
  }
  .card--front { top: 140px; }
  .card--back { top: 500px; }

  .company-name {
    position: absolute;
    right: 40px; top: 150px;
    font-size: 36px; font-weight: 600;
    line-height: 1.2;
    letter-spacing: 1px;
    text-transform: uppercase;
    white-space: nowrap;
  }
  .service-band {
    position: absolute;
    left: 0; right: 0; top: 214px;
    height: 28px;
    background: var(--ink);
    display: flex; align-items: center; justify-content: flex-end;
    padding-right: 40px;
    color: var(--band-text);
    font-size: 14px;
    letter-spacing: 1.2px;
    text-transform: uppercase;
    white-space: nowrap;
  }
  .service-band .sep { font-size: 9px; margin: 0 6px; }

  .contact {
    position: absolute;
    left: 40px; top: 86px;
  }
  .contact__name { font-size: 32px; font-weight: 700; line-height: 1; }
  .contact__title { font-size: 20px; color: var(--ink-soft); margin-top: 4px; }
  .contact__list { list-style: none; margin-top: 12px; }
  .contact__list li {
    display: flex; align-items: center; gap: 10px;
    font-size: 18px; line-height: 1.35; color: var(--ink-soft);
    white-space: nowrap;
  }
  .contact__list svg { width: 13px; height: 13px; flex: none; fill: var(--ink); }

  .horse-art {
    position: absolute;
    left: 300px; right: 0; top: 44px; bottom: 0;
    background: linear-gradient(160deg, var(--art-light), var(--art-dark));
    border-top-left-radius: 12px;
  }
</style>
</head>
<body>
<main class="canvas">
  <section class="card card--front">
    <h1 class="company-name">Cedar Brook Stables, LLC</h1>
    <div class="service-band">
      Equine Retirement<span class="sep">◆</span>Farm Sitting<span class="sep">◆</span>Short Term Board
    </div>
  </section>

  <section class="card card--back">
    <div class="horse-art" role="img" aria-label="Line drawing of a standing horse, head and forequarters"></div>
    <div class="contact">
      <h2 class="contact__name">Daniel Hayes</h2>
      <p class="contact__title">Founder &amp; CEO</p>
      <ul class="contact__list">
        <li><svg viewBox="0 0 24 24"><path d="M12 2a7 7 0 0 0-7 7c0 5 7 13 7 13s7-8 7-13a7 7 0 0 0-7-7zm0 9.5A2.5 2.5 0 1 1 12 6.5a2.5 2.5 0 0 1 0 5z"/></svg>Ashford, SC</li>
        <li><svg viewBox="0 0 24 24"><path d="M6.6 10.8a15 15 0 0 0 6.6 6.6l2.2-2.2a1 1 0 0 1 1-.25 11.4 11.4 0 0 0 3.6.57 1 1 0 0 1 1 1V20a1 1 0 0 1-1 1A17 17 0 0 1 3 4a1 1 0 0 1 1-1h3.5a1 1 0 0 1 1 1c0 1.25.2 2.45.57 3.57a1 1 0 0 1-.25 1z"/></svg>(123) 456-7890</li>
        <li><svg viewBox="0 0 24 24"><path d="M2 5h20v2.2l-10 7-10-7z M2 9.6l10 7 10-7V19H2z"/></svg>info@yourwebsite.com</li>
        <li><svg viewBox="0 0 24 24"><path d="M12 2a10 10 0 1 0 0 20 10 10 0 0 0 0-20zm6.9 6h-3a15 15 0 0 0-1.4-4A8 8 0 0 1 18.9 8zM12 4c.8 1.2 1.5 2.5 1.9 4h-3.8c.4-1.5 1.1-2.8 1.9-4zM4.3 14a8 8 0 0 1 0-4h3.4a16 16 0 0 0 0 4zm.8 2h3a15 15 0 0 0 1.4 4A8 8 0 0 1 5.1 16zm3-8h-3a8 8 0 0 1 4.4-4A15 15 0 0 0 8.1 8zM12 20c-.8-1.2-1.5-2.5-1.9-4h3.8c-.4 1.5-1.1 2.8-1.9 4zm2.3-6H9.7a14 14 0 0 1 0-4h4.6a14 14 0 0 1 0 4zm.2 6a15 15 0 0 0 1.4-4h3a8 8 0 0 1-4.4 4zm1.8-6a16 16 0 0 0 0-4h3.4a8 8 0 0 1 0 4z"/></svg>yourwebsite.com</li>
      </ul>
    </div>
  </section>
</main>
</body>
</html>
```